Bright Harbor Painters Banner

Create a banner that displays and reinforces Bright Harbor Painters’ brand identity while promoting our interior painting services. The banner will be displayed at indoor venues through the winter. The design should be clean, professional, and visually recognizable to both new and returning customers. See attached design brief & logo source files.

```html
<!DOCTYPE html>
<html lang="en">
<head>
<meta charset="utf-8">
<title>Bright Harbor Painters Banner</title>
<link href="https://fonts.googleapis.com/css2?family=Poppins:wght@600;700&display=swap" rel="stylesheet">
<style>
  :root {
    --stage: #6d7367;
    --banner-light: #eceded;
    --banner-mid: #e2e3e3;
    --ink: #434543;
    --green: #6b9a4b;
    --white: #ffffff;
  }
  * { margin: 0; padding: 0; box-sizing: border-box; }
  html, body { width: 1068px; height: 1200px; overflow: hidden; }
  body { background: var(--stage); font-family: "Poppins", sans-serif; position: relative; }

  .banner {
    position: absolute; left: 34px; top: 400px;
    width: 1000px; height: 400px;
    background: linear-gradient(100deg, var(--banner-light), var(--banner-mid));
    overflow: hidden;
    box-shadow: 0 12px 30px rgba(0,0,0,0.25);
  }
  .banner-shapes { position: absolute; inset: 0; }
  .painter-photo {
    position: absolute; left: 0; top: 0; width: 300px; height: 400px;
    background:
      radial-gradient(ellipse at 45% 20%, #d9b99e 0 9%, transparent 10%),
      linear-gradient(180deg, #e6e8e8 0%, #c9cdce 45%, #8a9294 75%, #6f777a 100%);
  }
  .headline { position: absolute; left: 190px; top: 22px; font-weight: 700; line-height: 1; letter-spacing: -1px; }
  .headline-top { display: block; font-size: 58px; color: var(--ink); }
  .headline-bottom { display: block; font-size: 59px; color: var(--green); margin-top: 2px; }
  .since {
    position: absolute; left: 340px; top: 150px; width: 450px; text-align: center;
    color: var(--white); font-weight: 700; font-size: 31px; letter-spacing: 7px; line-height: 36px;
  }
  .brand-name {
    position: absolute; left: 760px; top: 60px; width: 210px; text-align: center;
    color: var(--green); font-weight: 700; font-size: 30px; line-height: 1.05;
  }
  .services { position: absolute; top: 206px; list-style: none; color: var(--white); font-weight: 600; font-size: 27px; line-height: 40px; }
  .services li { display: flex; align-items: flex-start; gap: 14px; }
  .services svg { flex: none; margin-top: 11px; }
  .services-a { left: 364px; }
  .services-b { left: 564px; }
  .services-c { left: 766px; line-height: 34px; }
  .services-c li { line-height: 34px; }
  .services-c svg { margin-top: 8px; }
  .estimate { position: absolute; left: 256px; top: 305px; color: var(--ink); font-weight: 700; font-size: 25px; line-height: 32px; }
  .url-pill {
    position: absolute; left: 455px; top: 314px; width: 496px; height: 54px;
    background: var(--white); border-radius: 27px;
    display: flex; align-items: center; padding-left: 18px; gap: 18px;
  }
  .url { font-weight: 700; font-size: 34px; color: var(--ink); letter-spacing: -0.5px; }
  .url .domain { color: var(--green); }
</style>
</head>
<body>
  <section class="banner">
    <svg class="banner-shapes" width="1000" height="400" viewBox="0 0 1000 400" aria-hidden="true">
      <rect x="145" y="186" width="855" height="103" fill="var(--ink)"/>
      <rect x="145" y="184" width="855" height="3" fill="var(--green)"/>
      <path d="M330 187 C368 187 372 148 410 148 L700 148 C740 148 748 187 800 187 Z" fill="var(--green)"/>
    </svg>

    <div class="painter-photo" role="img" aria-label="Smiling painter in a hard hat and overalls rolling paint onto a wall"></div>

    <h1 class="headline">
      <span class="headline-top">TRUSTED LOCAL</span>
      <span class="headline-bottom">PROFESSIONALS</span>
    </h1>
    <p class="since">SINCE 2005</p>

    <p class="brand-name">BRIGHT HARBOR<br>PAINTERS</p>

    <ul class="services services-a">
      <li><svg width="18" height="18" viewBox="0 0 18 18"><circle cx="9" cy="9" r="8" fill="#fff" stroke="var(--green)" stroke-width="2"/><path d="M5 9.2l2.7 2.6L13 6.5" fill="none" stroke="var(--green)" stroke-width="2" stroke-linecap="round" stroke-linejoin="round"/></svg>Walls</li>
      <li><svg width="18" height="18" viewBox="0 0 18 18"><circle cx="9" cy="9" r="8" fill="#fff" stroke="var(--green)" stroke-width="2"/><path d="M5 9.2l2.7 2.6L13 6.5" fill="none" stroke="var(--green)" stroke-width="2" stroke-linecap="round" stroke-linejoin="round"/></svg>Ceilings</li>
    </ul>
    <ul class="services services-b">
      <li><svg width="18" height="18" viewBox="0 0 18 18"><circle cx="9" cy="9" r="8" fill="#fff" stroke="var(--green)" stroke-width="2"/><path d="M5 9.2l2.7 2.6L13 6.5" fill="none" stroke="var(--green)" stroke-width="2" stroke-linecap="round" stroke-linejoin="round"/></svg>Trim</li>
      <li><svg width="18" height="18" viewBox="0 0 18 18"><circle cx="9" cy="9" r="8" fill="#fff" stroke="var(--green)" stroke-width="2"/><path d="M5 9.2l2.7 2.6L13 6.5" fill="none" stroke="var(--green)" stroke-width="2" stroke-linecap="round" stroke-linejoin="round"/></svg>Cabinets</li>
    </ul>
    <ul class="services services-c">
      <li><svg width="18" height="18" viewBox="0 0 18 18"><circle cx="9" cy="9" r="8" fill="#fff" stroke="var(--green)" stroke-width="2"/><path d="M5 9.2l2.7 2.6L13 6.5" fill="none" stroke="var(--green)" stroke-width="2" stroke-linecap="round" stroke-linejoin="round"/></svg><span>Drywall<br>Repair</span></li>
    </ul>

    <p class="estimate">Book a Free<br>Estimate at</p>
    <div class="url-pill">
      <svg width="26" height="26" viewBox="0 0 26 26" aria-hidden="true">
        <circle cx="13" cy="13" r="11" fill="none" stroke="var(--green)" stroke-width="2.4"/>
        <ellipse cx="13" cy="13" rx="5" ry="11" fill="none" stroke="var(--green)" stroke-width="2.2"/>
        <path d="M2 13h22M4 7.5h18M4 18.5h18" stroke="var(--green)" stroke-width="2.2"/>
      </svg>
      <span class="url">www.<span class="domain">bhpainters</span>.com</span>
    </div>
  </section>
</body>
</html>
```